New iOS App design for Boston Startup

We are looking for a new app design for our iPhone app. The current app's design feels outdated and we like to add lots of new functionality and a new navigation as well. A complete overhaul therefore!
We want you to design 5 screens that will have changed the most. The complete wireframes of these 5 pages are attached in the requirements document.
Once the winning design is selected we will award the winner with the designing all other screens (40-50 screens based on the same design). This will be a separate project worth $1000. The winning designer can get more follow up work if both sides are happy about the cooperation.
We will give feedback as soon as the first screen has been uploaded for review. Final decision will be made only after all 5 screens are finished.
We hope you give it your best!
Note: will only communicate through PixelHarbor (no skype),
Updates
Reason: Want to give designers a chance to submit their designs as I understand from some, the deadline is too close.
I have raised the award and introduced a 2nd price as well to make it worth your time. I hope you give it your best shot.
Reason: A few of you have asked for an extension of the deadline as time is running out. I will extend by one day. Tell me if you need more.
Industry/Entity Type
Startup
Requirements
Must have
- At least 1 screen before we can give you feedback.
Nice to have
- multiple options of 1 screen to get to a desirable design

```html
<!DOCTYPE html>
<html lang="en">
<head>
<meta charset="utf-8">
<title>Timeline</title>
<link rel="stylesheet" href="https://fonts.googleapis.com/css2?family=Roboto:wght@300;400;500&display=swap">
<style>
  :root {
    --status-bg: #000000;
    --header-red: #f05454;
    --white: #ffffff;
    --text-dark: #3d3d3d;
    --text-black: #111111;
    --button-orange: #f9b21f;
    --progress-green: #3fbf4f;
    --progress-grey: #cfcfcf;
    --ahead-orange: #f9b128;
    --behind-blue: #3e9ae2;
    --line-navy: #0e4384;
    --dot-green: #3cbf4a;
    --marker-red: #d9141c;
    --tab-grey: #5e5e5e;
    --divider: #dddddd;
  }
  html, body {
    margin: 0;
    padding: 0;
    width: 676px;
    height: 1200px;
    overflow: hidden;
    background: var(--white);
    font-family: "Roboto", "Helvetica Neue", Arial, sans-serif;
  }
  .screen {
    position: relative;
    width: 640px;
    height: 1136px;
    transform: scale(1.05625);
    transform-origin: 0 0;
    background: var(--white);
  }
  .status-bar {
    position: absolute; left: 0; top: 0; width: 640px; height: 40px;
    background: var(--status-bg); color: var(--white);
    font-weight: 500; font-size: 24px;
  }
  .status-bar .signal { position: absolute; left: 6px; top: 12px; }
  .status-bar .carrier { position: absolute; left: 52px; top: 6px; letter-spacing: 0.5px; }
  .status-bar .clock { position: absolute; left: 0; width: 640px; top: 6px; text-align: center; }
  .status-bar .status-icons { position: absolute; right: 10px; top: 9px; }

  .app-header {
    position: absolute; left: 0; top: 40px; width: 640px; height: 90px;
    background: var(--header-red);
  }
  .back-button { position: absolute; left: 22px; top: 30px; }
  .app-header h1 {
    margin: 0; position: absolute; left: 0; width: 640px; top: 22px;
    text-align: center; color: var(--white); font-weight: 300; font-size: 38px;
  }

  .test-date {
    position: absolute; left: 24px; top: 160px; margin: 0;
    font-size: 26px; color: var(--text-dark); font-weight: 400;
  }
  .change-button {
    position: absolute; left: 443px; top: 153px; width: 170px; height: 40px;
    border-radius: 20px; background: var(--button-orange);
    box-shadow: 2px 4px 3px rgba(0,0,0,0.35), inset 0 0 0 2px #fff;
    font-size: 24px; color: var(--text-black); text-align: center; line-height: 38px;
    border: 0; padding: 0; font-family: inherit;
  }

  .completion-title {
    position: absolute; left: 0; width: 640px; top: 237px; margin: 0;
    text-align: center; font-size: 25px; color: var(--text-dark); font-weight: 400;
  }
  .progress-track {
    position: absolute; left: 23px; top: 283px; width: 595px; height: 10px;
    background: var(--progress-grey);
  }
  .progress-fill { width: 336px; height: 10px; background: var(--progress-green); }
  .progress-label {
    position: absolute; top: 311px; font-size: 23px; color: var(--text-black);
  }
  .progress-label.start { left: 23px; }
  .progress-label.mid { left: 292px; }
  .progress-label.end { right: 26px; }

  .chart-axis-label { position: absolute; font-size: 22px; color: var(--text-black); }
  .chart-axis-label.y-top { left: 22px; top: 410px; }
  .chart-axis-label.y-bottom { left: 50px; top: 802px; }
  .chart-axis-title {
    position: absolute; left: 62px; top: 633px; font-size: 25px; color: var(--text-dark);
    transform: translate(-50%, -50%) rotate(-90deg); white-space: nowrap;
  }
  .chart-x-label { position: absolute; top: 850px; font-size: 23px; color: var(--text-dark); }
  .chart-x-label.start { left: 103px; }
  .chart-x-label.mid { left: 325px; }
  .chart-x-label.end { left: 517px; }
  .schedule-chart { position: absolute; left: 0; top: 0; }
  .zone-label { fill: var(--white); font-size: 24px; font-family: "Roboto", "Helvetica Neue", Arial, sans-serif; }

  .tab-bar {
    position: absolute; left: 0; top: 1005px; width: 640px; height: 131px;
    border-top: 3px solid var(--divider); background: var(--white);
    display: flex;
  }
  .tab-item {
    flex: 1; position: relative; text-align: center; color: var(--tab-grey); font-size: 20px;
  }
  .tab-item svg { position: absolute; left: 50%; top: 30px; transform: translateX(-50%); }
  .tab-item span { position: absolute; left: 0; right: 0; top: 94px; }
</style>
</head>
<body>
<div class="screen">
  <div class="status-bar">
    <svg class="signal" width="40" height="16" viewBox="0 0 40 16" aria-hidden="true">
      <rect x="0" y="12" width="5" height="4" fill="#fff"/>
      <rect x="7" y="9" width="5" height="7" fill="#fff"/>
      <rect x="14" y="6" width="5" height="10" fill="#fff"/>
      <rect x="21" y="3" width="5" height="13" fill="#fff"/>
      <rect x="28" y="0" width="5" height="16" fill="#fff"/>
    </svg>
    <span class="carrier">NIMBUS&nbsp; 3G</span>
    <span class="clock">9:51 PM</span>
    <svg class="status-icons" width="76" height="22" viewBox="0 0 76 22" aria-hidden="true">
      <circle cx="10" cy="11" r="9" fill="#fff"/>
      <path d="M10 5 V11 H14" stroke="#000" stroke-width="2" fill="none"/>
      <rect x="30" y="3" width="40" height="17" rx="2" fill="none" stroke="#fff" stroke-width="2"/>
      <rect x="33" y="6" width="34" height="11" fill="#fff"/>
      <rect x="71" y="8" width="3" height="7" fill="#fff"/>
    </svg>
  </div>

  <header class="app-header">
    <svg class="back-button" width="36" height="36" viewBox="0 0 36 36" aria-label="Back" role="img">
      <circle cx="18" cy="18" r="18" fill="#fff"/>
      <path d="M7 18 L17 9 V14 H28 V22 H17 V27 Z" fill="var(--header-red)"/>
    </svg>
    <h1>Timeline</h1>
  </header>

  <p class="test-date">Your Test date: 4 Nov 2013</p>
  <button class="change-button">change</button>

  <p class="completion-title">Completion :</p>
  <div class="progress-track"><div class="progress-fill"></div></div>
  <span class="progress-label start">0%</span>
  <span class="progress-label mid">48%</span>
  <span class="progress-label end">100%</span>

  <svg class="schedule-chart" width="640" height="900" viewBox="0 0 640 900" role="img" aria-label="Completion over time against schedule">
    <defs>
      <linearGradient id="diagShade" x1="0" y1="0" x2="1" y2="1">
        <stop offset="0" stop-color="#000" stop-opacity="0.25"/>
        <stop offset="1" stop-color="#000" stop-opacity="0"/>
      </linearGradient>
    </defs>
    <rect x="93" y="403" width="508" height="427" fill="var(--ahead-orange)" stroke="#7a5a10" stroke-opacity="0.5" stroke-width="2"/>
    <polygon points="93,830 601,403 601,830" fill="var(--behind-blue)"/>
    <line x1="93" y1="830" x2="601" y2="403" stroke="#5a4a20" stroke-opacity="0.35" stroke-width="3"/>
    <text class="zone-label" x="164" y="483">Ahead of schedule</text>
    <text class="zone-label" x="368" y="774">Behind schedule</text>
    <polyline points="93,779 205,723 336,671 405,563" fill="none" stroke="var(--line-navy)" stroke-width="9" stroke-linejoin="round"/>
    <circle cx="205" cy="723" r="14" fill="var(--dot-green)" stroke="#fff" stroke-width="3"/>
    <circle cx="336" cy="671" r="14" fill="var(--dot-green)" stroke="#fff" stroke-width="3"/>
    <circle cx="405" cy="563" r="20" fill="var(--marker-red)"/>
    <circle cx="405" cy="563" r="12" fill="var(--line-navy)" stroke="#fff" stroke-width="3"/>
  </svg>

  <span class="chart-axis-label y-top">100%</span>
  <span class="chart-axis-label y-bottom">0%</span>
  <span class="chart-axis-title">Completion</span>
  <span class="chart-x-label start">1 Sep 13</span>
  <span class="chart-x-label mid">time</span>
  <span class="chart-x-label end">4 Nov 13</span>

  <nav class="tab-bar">
    <div class="tab-item">
      <svg width="66" height="50" viewBox="0 0 66 50" aria-hidden="true">
        <rect x="4" y="4" width="50" height="8" rx="2" fill="#666"/>
        <rect x="1" y="16" width="62" height="8" rx="2" fill="#666"/>
        <rect x="8" y="28" width="52" height="8" rx="2" fill="#666"/>
        <rect x="3" y="40" width="56" height="8" rx="2" fill="#666"/>
      </svg>
      <span>Theory</span>
    </div>
    <div class="tab-item">
      <svg width="46" height="56" viewBox="0 0 46 56" aria-hidden="true">
        <rect x="2" y="6" width="42" height="48" rx="3" fill="none" stroke="#666" stroke-width="4"/>
        <rect x="14" y="1" width="18" height="10" rx="2" fill="#666"/>
        <rect x="12" y="20" width="26" height="3" fill="#666"/>
        <rect x="12" y="28" width="26" height="3" fill="#666"/>
        <rect x="12" y="36" width="26" height="3" fill="#666"/>
        <rect x="12" y="44" width="26" height="3" fill="#666"/>
      </svg>
      <span>Practice</span>
    </div>
    <div class="tab-item">
      <svg width="54" height="50" viewBox="0 0 54 50" aria-hidden="true">
        <path d="M27 2 L52 24 H45 V48 H33 V32 H21 V48 H9 V24 H2 Z" fill="#666"/>
      </svg>
      <span>Home</span>
    </div>
    <div class="tab-item">
      <svg width="56" height="40" viewBox="0 0 56 40" aria-hidden="true">
        <path d="M12 6 H44 C54 6 56 20 54 30 C52 40 44 38 38 30 H18 C12 38 4 40 2 30 C0 20 2 6 12 6 Z" fill="#666"/>
        <rect x="11" y="16" width="12" height="4" fill="#fff"/>
        <rect x="15" y="12" width="4" height="12" fill="#fff"/>
        <circle cx="38" cy="15" r="3" fill="#fff"/>
        <circle cx="45" cy="20" r="3" fill="#fff"/>
      </svg>
      <span>Games</span>
    </div>
    <div class="tab-item">
      <svg width="50" height="56" viewBox="0 0 50 56" aria-hidden="true">
        <rect x="2" y="6" width="40" height="48" fill="none" stroke="#666" stroke-width="4"/>
        <rect x="10" y="18" width="24" height="3" fill="#666"/>
        <rect x="10" y="26" width="24" height="3" fill="#666"/>
        <rect x="10" y="34" width="24" height="3" fill="#666"/>
        <rect x="10" y="42" width="24" height="3" fill="#666"/>
        <path d="M28 8 L35 15 L48 1" fill="none" stroke="#666" stroke-width="5"/>
      </svg>
      <span>Test</span>
    </div>
  </nav>
</div>
</body>
</html>
```